Medical Billing Company Needs a Business Card Design

We need a business card design for a Florida based medical billing company called 'Clinicians Keystone Solutions'. We specialize in providing revenue cycle management services to physician and therapist offices (we're basically their back-office processing partner for providing billing software, claims submissions, A/R follow-up and patient statements & collections. Our logo is red and blue-ish, so make sure that whatever other elements are used will match appropriately. Our current business card design has a too small font size. I'd like to project an image that shows we are modern & reliable. On a side note, I'm planning on using ZUB for printing these cards.

Target Market(s)

Office managers, physicians, therapists

Industry/Entity Type

Printing

Requirements
Must have
• Logo
Name of Employee
Phone
Fax
E-mail
Website

```html
<!DOCTYPE html>
<html lang="en">
<head>
<meta charset="utf-8">
<title>Clinicians Keystone Solutions – Business Card</title>
<link rel="stylesheet" href="https://fonts.googleapis.com/css2?family=Open+Sans:wght@400;600;700&display=swap">
<style>
  :root {
    --page: #ece9e4;
    --card: #f6f2ea;
    --navy: #26225f;
    --brand: #2e2a6b;
    --red: #9b1c23;
    --gold: #e6cfa4;
    --white: #ffffff;
  }
  * { margin: 0; padding: 0; box-sizing: border-box; }
  html, body {
    width: 1200px; height: 1106px; overflow: hidden;
    background: var(--page);
    font-family: "Open Sans", Arial, sans-serif;
  }
  .card {
    position: absolute;
    background: var(--card);
    overflow: hidden;
    box-shadow: 0 2px 10px rgba(0,0,0,0.12);
  }
  .card-front { left: 190px; top: 143px; width: 635px; height: 352px; }
  .card-back  { left: 279px; top: 613px; width: 600px; height: 352px; }
  .band { position: absolute; inset: 0; width: 100%; height: 100%; }
  .wordmark {
    position: absolute; left: 0; right: 0;
    text-align: center;
    color: var(--brand);
    font-weight: 400;
    font-size: 27px;
    letter-spacing: 1.5px;
    white-space: nowrap;
  }
  .card-front .wordmark { top: 86px; }
  .card-back .wordmark { top: 86px; transform: scaleX(-1); opacity: 0.9; }
  .identity {
    position: absolute; right: 348px; top: 244px;
    text-align: right; color: var(--white);
  }
  .identity .person { font-size: 19px; font-weight: 700; line-height: 24px; }
  .identity .role { font-size: 15px; line-height: 22px; margin-bottom: 4px; }
  .identity .address { font-size: 15px; line-height: 23px; }
  .divider {
    position: absolute; left: 297px; top: 252px;
    width: 1.5px; height: 62px;
    background: linear-gradient(transparent, var(--white), transparent);
  }
  .contacts {
    position: absolute; left: 314px; top: 246px;
    list-style: none; color: var(--white); font-size: 15px;
  }
  .contacts li { display: flex; align-items: center; height: 23.5px; }
  .contacts svg { width: 14px; height: 14px; margin-right: 8px; flex: none; }
  .site-url {
    position: absolute; left: 0; right: 0; top: 286px;
    text-align: center; color: var(--white);
    font-size: 23px; letter-spacing: 1.6px;
  }
</style>
</head>
<body>

<section class="card card-front" aria-label="Card front">
  <svg class="band" viewBox="0 0 635 352" preserveAspectRatio="none" aria-hidden="true">
    <path d="M0 290 Q317.5 118 635 290 L635 300 Q317.5 134 0 300 Z" fill="var(--red)"/>
    <path d="M0 300 Q317.5 134 635 300 L635 306 Q317.5 146 0 306 Z" fill="var(--gold)"/>
    <path d="M0 306 Q317.5 148 635 306 L635 352 L0 352 Z" fill="var(--navy)"/>
  </svg>
  <div class="wordmark">CLINICIANS KEYSTONE</div>
  <div class="identity">
    <div class="person">Your Name</div>
    <div class="role">Title</div>
    <div class="address">Street Name, City Name<br>State Zip Code</div>
  </div>
  <div class="divider"></div>
  <ul class="contacts">
    <li><svg viewBox="0 0 16 16"><path d="M4 1.5 L6.5 4.5 L5 6.5 Q6.5 9.5 9.5 11 L11.5 9.5 L14.5 12 L13 14.5 Q5 14 1.5 3 Z" fill="none" stroke="#fff" stroke-width="1.4"/></svg>123-456-0789</li>
    <li><svg viewBox="0 0 16 16"><rect x="4.5" y="1" width="7" height="14" rx="1.2" fill="#fff"/><rect x="5.8" y="3" width="4.4" height="6" fill="var(--navy)"/></svg>123-456-0789</li>
    <li><svg viewBox="0 0 16 16"><rect x="1.5" y="4" width="13" height="9" rx="1" fill="#fff"/><path d="M1.5 4.5 L8 9 L14.5 4.5" fill="none" stroke="var(--navy)" stroke-width="1.3"/></svg>info@clinicianskeystone.com</li>
    <li><svg viewBox="0 0 16 16"><circle cx="8" cy="8" r="6.5" fill="none" stroke="#fff" stroke-width="1.4"/><ellipse cx="8" cy="8" rx="2.8" ry="6.5" fill="none" stroke="#fff" stroke-width="1.2"/><path d="M1.5 8 H14.5" stroke="#fff" stroke-width="1.2"/></svg>www.clinicianskeystone.com</li>
  </ul>
</section>

<section class="card card-back" aria-label="Card back">
  <svg class="band" viewBox="0 0 600 352" preserveAspectRatio="none" aria-hidden="true">
    <path d="M0 288 Q300 120 600 288 L600 296 Q300 134 0 296 Z" fill="var(--red)"/>
    <path d="M0 296 Q300 134 600 296 L600 300 Q300 144 0 300 Z" fill="var(--gold)"/>
    <path d="M0 300 Q300 146 600 300 L600 352 L0 352 Z" fill="var(--navy)"/>
  </svg>
  <div class="wordmark">CLINICIANS KEYSTONE</div>
  <div class="site-url">www.clinicianskeystone.com</div>
</section>

</body>
</html>
```